Flat Belly Design Graphics for Social

I want to create 9 social media graphics (new Instagram size 4:5 (1080 x 1350 pixels) focusing on our Flat Belly Graphics, using the pics attached. Use the attached pics, NO RANDOM STOCK PHOTOGRAPHY. For the color scheme of the graphics, the color palette is attached. YOU MUST POST ALL 9 GRAPHICS IN ONE ENTRY.
Using the 3 titles below, create one set of graphics. 1) with all text, then for the others, use the pictures as detailed below in IMPORTANT:
1. Ten-Week Bright Morning Reboot
2. The Quick Garden Kitchen Menu Guide
3. Studio Habits for Lasting Energy Past Midlife - Zero Gym Needed
IMPORTANT:
Only use RK Pic 1 and RK Pic 2 with the title, Ten-Week Bright Morning Reboot
Only use meal plan1 and meal plan2 pics with the title, Quick Garden Kitchen Menu Guide
Only use studio habits 1 and studio habits 2 pics with the title, Studio Habits for Lasting Energy Past Midlife - Zero Gym Needed
women over 40

```html
<!DOCTYPE html>
<html lang="en">
<head>
<meta charset="utf-8">
<title>Wellness Social Graphics Set</title>
<link href="https://fonts.googleapis.com/css2?family=Montserrat:wght@600;700;800&family=Playfair+Display:ital,wght@0,700;0,800;1,700;1,800&display=swap" rel="stylesheet">
<style>
  :root {
    --green: #2f4c4a;
    --pink: #e097ae;
    --pink-light: #f6b8ca;
    --pink-pale: #f9dbe4;
    --white: #ffffff;
    --page: #eceef0;
    --sans: "Montserrat", Arial, sans-serif;
    --serif: "Playfair Display", Georgia, serif;
  }
  * { box-sizing: border-box; margin: 0; padding: 0; }
  html, body { width: 966px; height: 1200px; overflow: hidden; background: var(--page); }
  .sheet { position: relative; width: 966px; height: 1200px; }
  .card {
    position: absolute; width: 413px; height: 516px; overflow: hidden;
    background: var(--white); box-shadow: 0 2px 6px rgba(0,0,0,0.08);
  }
  .card--menu { left: 45px; top: 55px; }
  .card--studio-photo { left: 504px; top: 55px; }
  .card--studio-text { left: 45px; top: 618px; }
  .card--reboot { left: 504px; top: 618px; }
  .line {
    position: absolute; left: 0; right: 0; text-align: center;
    line-height: 1; transform: translateY(-50%); white-space: nowrap;
  }
  .shape { position: absolute; left: 0; top: 0; }

  /* Menu guide card */
  .photo-food {
    position: absolute; left: 0; top: 0; width: 413px; height: 330px;
    background: linear-gradient(135deg, #6b4630 0%, #8b5a3c 35%, #c86a5a 55%, #7a9a55 75%, #5b3b28 100%);
  }
  .menu-title { font-family: var(--sans); font-weight: 700; color: var(--green); font-size: 41px; letter-spacing: -0.5px; }
  .menu-accent { font-family: var(--serif); font-style: italic; font-weight: 800; color: var(--pink); font-size: 40px; letter-spacing: -1px; }
  .gradient-rule {
    position: absolute; left: 0; right: 0; bottom: 0; height: 7px;
    background: linear-gradient(90deg, var(--pink) 0%, #f3e6ea 35%, #f3f3f3 55%, var(--green) 100%);
  }

  /* Studio photo card */
  .photo-friends {
    position: absolute; left: 15px; top: 130px; width: 382px; height: 250px;
    background: linear-gradient(120deg, #4a3226 0%, #b88a70 40%, #efe6e0 65%, #c9977a 85%, #5a3a2c 100%);
  }
  .studio-head { font-family: var(--sans); font-weight: 700; color: var(--white); font-size: 34px; }
  .studio-head em { font-family: var(--serif); font-style: italic; font-weight: 700; color: var(--pink); }
  .band-small { font-family: var(--sans); font-weight: 700; color: var(--white); font-size: 30px; }
  .band-big { font-family: var(--sans); font-weight: 800; color: var(--white); font-size: 50px; }

  /* Studio text card */
  .card--studio-text {
    background:
      radial-gradient(circle at 0% 55%, var(--pink-pale) 0%, rgba(249,219,228,0) 30%),
      linear-gradient(225deg, var(--green) 0%, #3d5452 18%, #9d7a88 42%, var(--pink-light) 65%, var(--pink) 100%);
  }
  .kicker { font-family: var(--sans); font-weight: 700; color: var(--white); font-size: 30px; letter-spacing: 1px; }
  .kicker-big { font-family: var(--sans); font-weight: 800; color: var(--white); font-size: 56px; letter-spacing: 1px; }
  .serif-white { font-family: var(--serif); font-weight: 700; color: var(--white); text-shadow: 0 2px 3px rgba(0,0,0,0.3); }
  .serif-mid { font-size: 34px; }
  .serif-big { font-size: 48px; letter-spacing: -0.5px; }

  /* Reboot card */
  .reboot-serif { font-family: var(--serif); font-weight: 800; color: var(--green); font-size: 74px; letter-spacing: -2px; }
  .reboot-accent { font-family: var(--serif); font-style: italic; font-weight: 800; color: var(--pink); font-size: 70px; letter-spacing: -3px; }
  .reboot-band { font-family: var(--sans); font-weight: 800; color: var(--white); font-size: 62px; }
</style>
</head>
<body>
<main class="sheet">

  <!-- Menu guide -->
  <section class="card card--menu">
    <div class="photo-food" role="img" aria-label="Overhead photo of healthy foods and a meal plan sheet on a wooden table"></div>
    <svg class="shape" width="413" height="516" viewBox="0 0 413 516">
      <path d="M0 314 C90 280 200 290 300 310 C350 320 390 320 413 316 L413 516 L0 516 Z" fill="#ffffff"/>
      <path d="M0 314 C90 280 200 290 300 310 C350 320 390 320 413 316" fill="none" stroke="#e097ae" stroke-width="3"/>
    </svg>
    <div class="line menu-title" style="top:358px;">The Quick Garden</div>
    <div class="line menu-accent" style="top:413px;">KITCHEN MENU</div>
    <div class="line menu-title" style="top:466px;">Guide</div>
    <div class="gradient-rule"></div>
  </section>

  <!-- Studio habits, photo layout -->
  <section class="card card--studio-photo">
    <div class="photo-friends" role="img" aria-label="Photo of two women sharing a secret, one looking surprised"></div>
    <svg class="shape" width="413" height="516" viewBox="0 0 413 516">
      <polygon points="0,0 413,0 413,121 0,140" fill="#2f4c4a"/>
      <polygon points="0,140 413,121 413,128 0,148" fill="#ffffff"/>
      <polygon points="0,371 413,346 413,516 0,516" fill="#e097ae"/>
    </svg>
    <div class="line studio-head" style="top:43px;">Studio <em>HABITS</em></div>
    <div class="line studio-head" style="top:96px;">for Lasting Energy</div>
    <div class="line band-small" style="top:394px;">Past Midlife -</div>
    <div class="line band-big" style="top:438px;">ZERO GYM</div>
    <div class="line band-small" style="top:481px;">NEEDED</div>
  </section>

  <!-- Studio habits, text layout -->
  <section class="card card--studio-text">
    <svg class="shape" width="413" height="516" viewBox="0 0 413 516">
      <path d="M345 40 Q348 59 366 62 Q348 65 345 84 Q342 65 324 62 Q342 59 345 40 Z" fill="#ffffff"/>
      <path d="M364 68 Q366 78 376 80 Q366 82 364 92 Q362 82 352 80 Q362 78 364 68 Z" fill="#ffffff"/>
      <path d="M39 426 Q42 445 60 448 Q42 451 39 470 Q36 451 18 448 Q36 445 39 426 Z" fill="#ffffff"/>
      <path d="M58 456 Q60 466 70 468 Q60 470 58 480 Q56 470 46 468 Q56 466 58 456 Z" fill="#ffffff"/>
    </svg>
    <div class="line kicker" style="top:58px;">STUDIO</div>
    <div class="line kicker-big" style="top:111px;">HABITS</div>
    <div class="line serif-white serif-mid" style="top:234px;">For Lasting Energy</div>
    <div class="line serif-white serif-mid" style="top:282px;">Past Midlife -</div>
    <div class="line serif-white serif-big" style="top:352px;">ZERO GYM</div>
    <div class="line serif-white serif-big" style="top:418px;">NEEDED</div>
  </section>

  <!-- Reboot -->
  <section class="card card--reboot">
    <svg class="shape" width="413" height="516" viewBox="0 0 413 516">
      <path d="M0 292 C50 318 110 312 180 302 C270 288 350 268 413 284 L413 516 L0 516 Z" fill="#2f4c4a"/>
    </svg>
    <div class="line reboot-serif" style="top:62px;">Ten-Week</div>
    <div class="line reboot-serif" style="top:146px;">BRIGHT</div>
    <div class="line reboot-accent" style="top:226px;">MORNING</div>
    <div class="line reboot-band" style="top:400px;">REBOOT</div>
  </section>

</main>
</body>
</html>
```